Velvet Pressings Techno Label Business Card

I'm looking for a very clean business card for my Velvet Pressings music label. The label focusses on techno music. The card should include:

• my name : Tomas Brandt as "Founder & CEO"
• email address: tomas@velvet-pressings.example
• web: www.velvet-pressings.example
• facebook logo + /velvetpress
• twitter logo + /velvetpress
• soundcloud logo + /velvetpressings

Feel free to include your ideas! I'm looking forward to discuss about it.

Tomas

Industry/Entity Type

Business

Contact Information for Business Card

I don't like glossy cards. Prefer matt.

Requirements
Nice to have
• Maybe on one side the complete logo, other side just the icon.
Should not have
• Flashy stuff. Must be clean and business like style.

```html
<!DOCTYPE html>
<html lang="en">
<head>
<meta charset="utf-8">
<title>Velvet Pressings – Business Card</title>
<link rel="stylesheet" href="https://fonts.googleapis.com/css2?family=Open+Sans:wght@400;600;700&display=swap">
<style>
  :root {
    --stage: #3b3532;
    --label-orange: #f46200;
    --card-black: #111111;
    --ink-white: #ffffff;
    --ink-grey: #8a8a8a;
    --ink-soft: #b4b4b4;
  }
  * { box-sizing: border-box; margin: 0; padding: 0; }
  html, body {
    width: 1200px;
    height: 768px;
    overflow: hidden;
    background: var(--stage);
    font-family: "Open Sans", Arial, sans-serif;
  }
  .stage { position: relative; width: 1200px; height: 768px; }
  .card {
    position: absolute;
    width: 500px;
    height: 290px;
    box-shadow: 0 10px 30px rgba(0,0,0,.45);
  }

  /* Front side */
  .card-front { left: 70px; top: 239px; background: var(--label-orange); }
  .front-brand {
    position: absolute;
    left: 50%;
    top: 50%;
    transform: translate(-50%, -50%);
    display: flex;
    align-items: center;
    gap: 14px;
    white-space: nowrap;
  }
  .brand-dot {
    width: 30px;
    height: 30px;
    border-radius: 50%;
    background: var(--ink-white);
    flex: none;
  }
  .brand-name {
    font-weight: 700;
    font-size: 36px;
    letter-spacing: -0.5px;
    color: var(--ink-white);
  }

  /* Back side */
  .card-back { left: 630px; top: 239px; background: var(--card-black); }
  .back-brand {
    position: absolute;
    left: 34px;
    top: 131px;
    display: flex;
    align-items: center;
    gap: 9px;
    white-space: nowrap;
  }
  .back-brand-dot {
    width: 14px;
    height: 14px;
    border-radius: 50%;
    background: var(--label-orange);
    flex: none;
  }
  .back-brand-name {
    font-size: 18px;
    font-weight: 700;
    color: var(--label-orange);
    letter-spacing: -0.2px;
  }
  .divider {
    position: absolute;
    left: 218px;
    top: 60px;
    width: 1px;
    height: 170px;
    background: #2a2a2a;
  }
  .holder { position: absolute; left: 240px; top: 68px; }
  .holder-name {
    font-size: 19px;
    font-weight: 400;
    color: var(--label-orange);
    letter-spacing: 0.5px;
  }
  .holder-role { font-size: 11px; color: var(--ink-grey); margin-top: 1px; }
  .contact-list { position: absolute; left: 240px; top: 150px; list-style: none; }
  .contact-item {
    display: flex;
    align-items: center;
    gap: 10px;
    font-size: 13px;
    line-height: 20px;
    color: var(--ink-soft);
    white-space: nowrap;
  }
  .contact-icon { width: 12px; height: 12px; flex: none; }
</style>
</head>
<body>
<main class="stage">
  <section class="card card-front" aria-label="Card front">
    <div class="front-brand">
      <span class="brand-dot" aria-hidden="true"></span>
      <span class="brand-name">Velvet Pressings</span>
    </div>
  </section>

  <section class="card card-back" aria-label="Card back">
    <div class="back-brand">
      <span class="back-brand-dot" aria-hidden="true"></span>
      <span class="back-brand-name">Velvet Pressings</span>
    </div>
    <span class="divider" aria-hidden="true"></span>

    <div class="holder">
      <p class="holder-name">Tomas Brandt</p>
      <p class="holder-role">Founder &amp; CEO</p>
    </div>

    <ul class="contact-list">
      <li class="contact-item">
        <svg class="contact-icon" viewBox="0 0 12 12" aria-hidden="true">
          <rect x="0.5" y="2" width="11" height="8" fill="var(--label-orange)"/>
          <path d="M0.5 2 L6 6.5 L11.5 2" fill="none" stroke="var(--card-black)" stroke-width="1.2"/>
        </svg>
        tomas@velvet-pressings.example
      </li>
      <li class="contact-item">
        <svg class="contact-icon" viewBox="0 0 12 12" aria-hidden="true">
          <circle cx="6" cy="6" r="5.5" fill="var(--label-orange)"/>
          <ellipse cx="6" cy="6" rx="2.3" ry="5.5" fill="none" stroke="var(--card-black)" stroke-width="1"/>
          <line x1="0.5" y1="6" x2="11.5" y2="6" stroke="var(--card-black)" stroke-width="1"/>
        </svg>
        www.velvet-pressings.example
      </li>
      <li class="contact-item">
        <!-- generic share icon -->
        <svg class="contact-icon" viewBox="0 0 12 12" aria-hidden="true">
          <line x1="3" y1="6" x2="9" y2="2.5" stroke="var(--label-orange)" stroke-width="1.3"/>
          <line x1="3" y1="6" x2="9" y2="9.5" stroke="var(--label-orange)" stroke-width="1.3"/>
          <circle cx="3" cy="6" r="2" fill="var(--label-orange)"/>
          <circle cx="9" cy="2.5" r="2" fill="var(--label-orange)"/>
          <circle cx="9" cy="9.5" r="2" fill="var(--label-orange)"/>
        </svg>
        /velvetpress
      </li>
      <li class="contact-item">
        <!-- generic speech bubble icon -->
        <svg class="contact-icon" viewBox="0 0 12 12" aria-hidden="true">
          <path d="M1 1.5 H11 V8.5 H5 L2.5 11 V8.5 H1 Z" fill="var(--label-orange)"/>
        </svg>
        /velvetpress
      </li>
      <li class="contact-item">
        <!-- generic audio level bars icon -->
        <svg class="contact-icon" viewBox="0 0 12 12" aria-hidden="true">
          <rect x="0.5" y="5" width="2" height="6" fill="var(--label-orange)"/>
          <rect x="3.5" y="2" width="2" height="9" fill="var(--label-orange)"/>
          <rect x="6.5" y="4" width="2" height="7" fill="var(--label-orange)"/>
          <rect x="9.5" y="1" width="2" height="10" fill="var(--label-orange)"/>
        </svg>
        /velvetpressings
      </li>
    </ul>
  </section>
</main>
</body>
</html>
```